Website Design for a holiday home letting busines

We require a redesign of our present website www.pinebrookstays.com. We want the website to stand out and look professional and clean to make holiday hunters want to book a caravan or lodge holiday with us. Our logo is red however we DO NOT want the website to be red. We want a natural colour scheme.

The final design should communicate that we are a professional company to book with.

On the home page we require;
Overview of company
Photo
Search box for holiday (check in)
Late Deals
Reviews
News

We would like the following pages designed; home page, available dates page, caravans page, content page.

The website should be responsive for smart phones. One website I do like is http://www.verdoliso.be/nl/

Target Market(s)

Families

Industry/Entity Type

Travel

Number of Pages Required

5+ page

Font styles to use
Serif

Requirements
Must have
• The project must be responsive for mobile phones and tablets.
• Ability to search for holiday home holidays
• We want a natural colour scheme.
Nice to have
• A style we like is http://www.verdoliso.be/nl/
Should not have
• Do not use red as a colour for the website. Our logo is red so this is the only time we want this used.

```html
<!DOCTYPE html>
<html lang="en">
<head>
<meta charset="utf-8">
<title>Pinebrook Stays – Private Holiday Rentals</title>
<link href="https://fonts.googleapis.com/css2?family=Lora:wght@400;700&family=Open+Sans:wght@400;600;700&display=swap" rel="stylesheet">
<style>
:root{
  --teal:#5ec6c1;
  --teal-dark:#3fa9a4;
  --teal-pale:#e2f4f3;
  --ink:#333;
  --muted:#777;
  --line:#d7e9e8;
  --footer:#2e2f31;
  --footer-deep:#232426;
  --white:#fff;
  --brand:#c8262c;
}
*{box-sizing:border-box;margin:0;padding:0}
html,body{width:1200px;height:3288px;overflow:hidden}
body{font-family:"Open Sans",Arial,sans-serif;color:var(--ink);background:var(--white);font-size:13px}
h1,h2,h3,h4{font-family:"Lora",Georgia,serif;font-weight:400}
.wrap{width:960px;margin:0 auto;position:relative}

/* header */
.site-header{height:72px}
.site-header .wrap{display:flex;align-items:center;justify-content:space-between;height:72px}
.brand{display:flex;align-items:center;gap:10px}
.brand-mark{width:34px;height:34px;background:var(--brand);border-radius:4px}
.brand-name{font-family:"Lora",Georgia,serif;font-size:22px;color:var(--brand)}
.brand-sub{font-size:10px;color:var(--muted);display:block;font-family:"Open Sans",sans-serif}
.contact-top{display:flex;gap:30px;font-size:12px;color:var(--muted)}
.contact-top span{display:flex;align-items:center;gap:8px}
.icon-dot{width:22px;height:22px;border-radius:50%;background:var(--teal);display:inline-flex;align-items:center;justify-content:center}

/* hero */
.hero{height:616px;position:relative;background:linear-gradient(120deg,#2f8f95 0%,#5ec6c1 40%,#9fd8d5 65%,#efe6d6 82%,#c9b79d 100%)}
.main-nav{position:absolute;top:24px;left:120px;right:120px;height:34px;background:rgba(255,255,255,.92);display:flex}
.main-nav a{font-size:12px;color:var(--ink);text-decoration:none;padding:0 15px;line-height:34px}
.main-nav a.active{background:var(--teal);color:var(--white)}
.hero-caption{position:absolute;left:120px;top:300px;width:540px;padding:22px 30px;background:rgba(255,255,255,.35);text-align:center}
.hero-caption h1{font-size:38px;color:var(--white)}
.hero-caption p{font-family:"Lora",serif;color:var(--white);font-size:17px;margin-top:8px;line-height:1.4}
.side-tab{position:absolute;right:0;top:250px;width:30px;height:120px;background:var(--white);display:flex;align-items:center;justify-content:center}
.side-tab span{transform:rotate(90deg);font-size:11px;letter-spacing:2px;white-space:nowrap;color:var(--teal-dark)}

/* search */
.search-band{height:104px;background:var(--teal-pale);display:flex;align-items:center}
.search-band .wrap{display:flex;gap:24px;align-items:center}
.field{flex:1;height:44px;background:var(--white);border:1px solid var(--line);padding:0 16px;line-height:44px;color:#aaa;font-size:12px;display:flex;justify-content:space-between}
.btn{display:inline-block;background:var(--teal);color:var(--white);font-size:12px;font-weight:600;letter-spacing:1px;text-transform:uppercase;text-align:center}
.search-band .btn{width:240px;height:44px;line-height:44px}

/* overview */
.overview{height:388px;text-align:center;padding-top:48px}
.section-title{font-size:30px;letter-spacing:1px;text-transform:uppercase}
.rule{width:540px;height:1px;background:var(--line);margin:14px auto 26px}
.overview p{width:820px;margin:0 auto;font-size:13px;line-height:22px;color:var(--muted)}
.overview .btn{margin-top:26px;padding:12px 34px;border-radius:4px;box-shadow:0 3px 0 var(--teal-dark)}

/* caravans */
.caravans{height:600px;background:var(--teal-pale);padding-top:60px}
.caravans .section-title,.deals .section-title{text-align:left;font-size:28px}
.card-row{display:flex;gap:16px;margin-top:60px}
.card{width:304px;background:var(--white);text-align:center;box-shadow:0 2px 6px rgba(0,0,0,.08)}
.card-photo{height:170px;position:relative;overflow:hidden}
.card-photo svg{position:absolute;left:0;bottom:0}
.card h3{font-size:18px;text-transform:uppercase;margin-top:4px}
.card p{font-size:12px;color:var(--muted);line-height:18px;padding:8px 40px 0;height:44px}
.meta{display:flex;justify-content:center;gap:16px;font-size:10px;color:var(--muted);margin:14px 20px;border-top:1px solid var(--line);padding-top:10px}
.meta i{display:inline-block;width:10px;height:10px;background:var(--teal);border-radius:2px;margin-right:4px;vertical-align:-1px}
.card .btn{display:block;height:34px;line-height:34px}

/* deals */
.deals{height:460px;padding-top:48px}
.deal-row{display:flex;gap:16px;margin-top:46px}
.deal{width:304px;text-align:center}
.deal-photo{height:180px;position:relative;border-bottom:3px solid var(--teal)}
.deal-photo .btn{position:absolute;left:50%;top:56px;transform:translateX(-50%);padding:10px 20px;border-radius:3px}
.deal h3{font-size:17px;text-transform:uppercase;margin-top:16px}
.deal .dates{font-size:11px;margin-top:6px;font-weight:600}
.deal .dates em{font-style:normal;color:var(--teal-dark)}

/* feeds */
.feeds{height:770px;background:var(--teal-pale);padding-top:40px}
.feed-row{display:flex;gap:12px}
.feed{flex:1;background:var(--white);border:1px solid var(--line);height:700px;padding:0 18px}
.feed-head{background:var(--teal);color:var(--white);text-align:center;font-family:"Lora",serif;font-size:15px;text-transform:uppercase;height:42px;line-height:42px;margin:0 -18px 16px}
.entry{border-bottom:1px solid var(--line);padding:14px 0 18px}
.entry:last-child{border-bottom:0}
.entry h4{font-size:16px;text-transform:uppercase}
.stars{color:var(--teal);font-size:12px;margin:4px 0 8px;letter-spacing:2px}
.entry p{font-size:12px;line-height:19px;color:var(--muted)}
.entry.media{display:flex;gap:12px;flex-wrap:wrap}
.thumb{width:64px;height:56px;flex:none}
.entry.media .txt{flex:1}
.entry.media p{width:100%}
.fb-card{border:1px solid var(--line);padding:14px}
.fb-top{display:flex;gap:12px;align-items:center}
.fb-mark{width:56px;height:56px;background:var(--brand)}
.fb-name{font-family:"Lora",serif;font-size:16px;color:var(--brand)}
.fb-card p{font-size:11px;color:var(--muted);line-height:17px;margin-top:12px}
.fb-follow{display:inline-block;margin-top:12px;border:1px solid var(--line);padding:4px 10px;font-size:11px}
.fans{display:grid;grid-template-columns:repeat(4,1fr);gap:8px;margin-top:16px}
.fans div{height:58px;background:#c7d6d5}
.fans div:nth-child(2n){background:#b8c3bf}
.fans div:nth-child(3n){background:#d5cbbd}

/* footer */
.site-footer{height:246px;background:var(--footer);color:#ccc;padding-top:30px}
.site-footer .wrap{display:flex;justify-content:space-between}
.site-footer h3{color:var(--white);font-size:22px;margin-bottom:18px}
.f-contact li{list-style:none;font-size:12px;line-height:20px;display:flex;gap:10px;margin-bottom:10px}
.f-contact svg{flex:none;margin-top:3px}
.f-links{display:flex;gap:50px}
.f-links ul{list-style:none;font-size:12px;line-height:22px}
.news input{display:block;width:240px;height:34px;border:0;background:var(--white);margin-bottom:10px}
.news .btn{padding:9px 20px}
.socials{display:flex;gap:10px;margin-top:18px}
.socials span{width:30px;height:30px;border-radius:50%;background:var(--teal)}
.bottom-bar{height:32px;background:var(--footer-deep);color:#888;font-size:10px}
.bottom-bar .wrap{display:flex;justify-content:space-between;line-height:32px}
</style>
</head>
<body>

<header class="site-header">
  <div class="wrap">
    <div class="brand">
      <span class="brand-mark"></span>
      <div class="brand-name">Pinebrook Stays<span class="brand-sub">at Thornfield Hollow Holiday Park</span></div>
    </div>
    <div class="contact-top">
      <span><i class="icon-dot"><svg width="12" height="12" viewBox="0 0 24 24"><path fill="#fff" d="M6.6 10.8a15 15 0 0 0 6.6 6.6l2.2-2.2c.3-.3.7-.4 1-.2 1.1.4 2.3.6 3.6.6.6 0 1 .4 1 1V20c0 .6-.4 1-1 1A17 17 0 0 1 3 4c0-.6.4-1 1-1h3.5c.6 0 1 .4 1 1 0 1.3.2 2.5.6 3.6.1.3 0 .7-.2 1z"/></svg></i>01632 960 418</span>
      <span><i class="icon-dot"><svg width="12" height="12" viewBox="0 0 24 24"><path fill="#fff" d="M2 5h20v14H2zm2 2v.5l8 5 8-5V7l-8 5z"/></svg></i>hello@pinebrookstays.com</span>
    </div>
  </div>
</header>

<section class="hero" role="img" aria-label="Photo of lit candles on weathered turquoise wooden boards">
  <nav class="main-nav">
    <a class="active">Home</a><a>Review</a><a>Caravan &amp; Lodges</a><a>2017 Holidays</a><a>2018 Holidays</a><a>Payment Plans</a><a>Thornfield Hollow</a><a>Local Attractions</a><a>Contact Us</a>
  </nav>
  <div class="hero-caption">
    <h1>Private Holiday Rentals</h1>
    <p>Quality Lodge &amp; Caravan hire in Thornfield Hollow<br>Holiday Park. Book online today!</p>
  </div>
  <div class="side-tab"><span>CALL US</span></div>
</section>

<section class="search-band">
  <div class="wrap">
    <div class="field">CHECK IN DATE <span>▾</span></div>
    <div class="field">CHECK OUT DATE <span>▾</span></div>
    <div class="field">NO. OF GUESTS <span>▾</span></div>
    <span class="btn">Check Availability</span>
  </div>
</section>

<section class="overview">
  <h2 class="section-title">Overview of Company</h2>
  <div class="rule"></div>
  <p>We are a family run holiday letting business offering private lodges and caravans in a quiet, green corner of the countryside. Every home is cleaned, checked and prepared by our own team before you arrive, so your break starts the moment you open the door. We offer flexible short stays, full weeks and easy payment plans, and our friendly staff are always close by to help with local tips, bookings and anything you need during your stay with us.</p>
  <span class="btn">View More Info</span>
</section>

<section class="caravans">
  <div class="wrap">
    <h2 class="section-title">Our Caravans and Lodges</h2>
    <div class="card-row">
      <article class="card">
        <div class="card-photo" role="img" aria-label="Photo of a caravan living room with sofas" style="background:linear-gradient(135deg,#c9b59a,#8d7a66)"><svg width="304" height="40" viewBox="0 0 304 40"><path d="M0 40V10Q152 60 304 10v30z" fill="#fff"/></svg></div>
        <h3>The Ashcombe</h3>
        <p>Bright open lounge, two bedrooms and a private deck by the lake.</p>
        <div class="meta"><span><i></i>2 Bedrooms</span><span><i></i>6 Guests</span><span><i></i>Pets OK</span></div>
        <span class="btn">View More</span>
      </article>
      <article class="card">
        <div class="card-photo" role="img" aria-label="Photo of a lodge lounge with patio doors" style="background:linear-gradient(135deg,#d8cbb4,#9a8c77)"><svg width="304" height="40" viewBox="0 0 304 40"><path d="M0 40V10Q152 60 304 10v30z" fill="#fff"/></svg></div>
        <h3>The Harewood</h3>
        <p>Spacious lodge with patio doors, new kitchen and field views.</p>
        <div class="meta"><span><i></i>3 Bedrooms</span><span><i></i>8 Guests</span><span><i></i>Parking</span></div>
        <span class="btn">View More</span>
      </article>
      <article class="card">
        <div class="card-photo" role="img" aria-label="Photo of a caravan kitchen and dining area" style="background:linear-gradient(135deg,#e3dccf,#a9a093)"><svg width="304" height="40" viewBox="0 0 304 40"><path d="M0 40V10Q152 60 304 10v30z" fill="#fff"/></svg></div>
        <h3>The Linden</h3>
        <p>Cosy caravan with full kitchen, dining nook and garden area.</p>
        <div class="meta"><span><i></i>2 Bedrooms</span><span><i></i>4 Guests</span><span><i></i>Wi-Fi</span></div>
        <span class="btn">View More</span>
      </article>
    </div>
  </div>
</section>

<section class="deals">
  <div class="wrap">
    <h2 class="section-title">Late Deals</h2>
    <div class="deal-row">
      <article class="deal">
        <div class="deal-photo" role="img" aria-label="Photo of a caravan dining area" style="background:linear-gradient(135deg,#b7a48b,#75654f)"><span class="btn">Book Now</span></div>
        <h3>The Kestrel</h3>
        <p class="dates">FRIDAY 16 SEPTEMBER 2016 <em>£ 149 PER 2 NIGHTS</em></p>
      </article>
      <article class="deal">
        <div class="deal-photo" role="img" aria-label="Photo of a caravan lounge with sofas" style="background:linear-gradient(135deg,#a89479,#5f4f3f)"></div>
        <h3>The Kestrel</h3>
        <p class="dates">FRIDAY 23 SEPTEMBER 2016 <em>£ 149 PER 2 NIGHTS</em></p>
      </article>
      <article class="deal">
        <div class="deal-photo" role="img" aria-label="Photo of a caravan kitchen" style="background:linear-gradient(135deg,#d9d0c2,#8f8576)"></div>
        <h3>The Kestrel</h3>
        <p class="dates">FRIDAY 30 SEPTEMBER 2016 <em>£ 149 PER 2 NIGHTS</em></p>
      </article>
    </div>
  </div>
</section>

<section class="feeds">
  <div class="wrap feed-row">
    <div class="feed">
      <div class="feed-head">Latest Reviews</div>
      <div class="entry"><h4>Maren Ashby</h4><div class="stars">★★★★★</div><p>We loved our week here. The caravan was spotless, the beds were comfy and the children never wanted to leave the park. We are already planning next year.</p></div>
      <div class="entry"><h4>Delia Kowalczyk</h4><div class="stars">★★★★★</div><p>Lovely quiet spot with great walks right from the door. Booking was easy and the team were so helpful with everything we asked about.</p></div>
      <div class="entry"><h4>Ruth Pembers</h4><div class="stars">★★★★★</div><p>Warm, clean and well equipped lodge. Perfect for our family break and the dog was welcome too. Thank you for a relaxing stay.</p></div>
    </div>
    <div class="feed">
      <div class="feed-head">Blog Feed</div>
      <div class="entry media"><div class="thumb" role="img" aria-label="Blog photo of a lodge interior" style="background:#b9a68c"></div><div class="txt"><h4>Spring Opening</h4><div class="stars">12 MARCH 2016</div></div><p>The park reopens for the new season with fresh paint, new decking and a few extra dates for short breaks.</p></div>
      <div class="entry media"><div class="thumb" role="img" aria-label="Blog photo of a caravan lounge" style="background:#a2917a"></div><div class="txt"><h4>Walks Nearby</h4><div class="stars">28 APRIL 2016</div></div><p>Our favourite family walks within a short drive, from gentle riverside paths to views from the nearby hills.</p></div>
      <div class="entry media"><div class="thumb" role="img" aria-label="Blog photo of a caravan kitchen" style="background:#cfc5b6"></div><div class="txt"><h4>Payment Plans</h4><div class="stars">09 MAY 2016</div></div><p>Spread the cost of your holiday with our simple monthly payment plans, now open for next summer.</p></div>
    </div>
    <div class="feed">
      <div class="feed-head">Community Feed</div>
      <div class="fb-card">
        <div class="fb-top"><span class="fb-mark"></span><span class="fb-name">Pinebrook Stays</span></div>
        <p>Private lodges and caravans for family holidays at Thornfield Hollow. Book your stay online today.</p>
        <span class="fb-follow">Follow Us</span>
        <p>1,284 guests follow our updates</p>
        <div class="fans" role="img" aria-label="Grid of follower profile photos">
          <div></div><div></div><div></div><div></div><div></div><div></div><div></div><div></div>
        </div>
      </div>
    </div>
  </div>
</section>

<footer class="site-footer">
  <div class="wrap">
    <div class="f-contact">
      <h3>Contact us</h3>
      <ul>
        <li><svg width="12" height="14" viewBox="0 0 24 28"><path fill="#5ec6c1" d="M12 0a10 10 0 0 0-10 10c0 7.5 10 18 10 18s10-10.5 10-18A10 10 0 0 0 12 0zm0 14a4 4 0 1 1 0-8 4 4 0 0 1 0 8z"/></svg><span>Pinebrook Stays Ltd, Unit 4, Millbrook<br>Business Estate, Thornfield Road,<br>Eastfold EF4 2QX</span></li>
        <li><svg width="12" height="12" viewBox="0 0 24 24"><path fill="#5ec6c1" d="M6.6 10.8a15 15 0 0 0 6.6 6.6l2.2-2.2c.3-.3.7-.4 1-.2 1.1.4 2.3.6 3.6.6.6 0 1 .4 1 1V20c0 .6-.4 1-1 1A17 17 0 0 1 3 4c0-.6.4-1 1-1h3.5c.6 0 1 .4 1 1 0 1.3.2 2.5.6 3.6.1.3 0 .7-.2 1z"/></svg>01632 960 418</li>
        <li><svg width="12" height="12" viewBox="0 0 24 24"><path fill="#5ec6c1" d="M2 5h20v14H2zm2 2v.5l8 5 8-5V7l-8 5z"/></svg>hello@pinebrookstays.com</li>
      </ul>
    </div>
    <div>
      <h3>Footer links</h3>
      <div class="f-links">
        <ul><li>Home</li><li>Review</li><li>Caravan &amp; Lodges</li><li>2017 Holidays</li><li>2018 Holidays</li><li>Payment Plans</li></ul>
        <ul><li>Thornfield Hollow</li><li>Local Attractions</li><li>Contact Us</li></ul>
      </div>
    </div>
    <div class="news">
      <h3>News letter</h3>
      <input type="text" aria-label="Email address">
      <span class="btn">Subscribe</span>
      <div class="socials"><span></span><span></span><span></span><span></span></div>
    </div>
  </div>
</footer>
<div class="bottom-bar"><div class="wrap"><span>copyright@pinebrookstays.com 2016</span><span>Top</span></div></div>

</body>
</html>
```